Organization and people consulting firm needs a website design

I need a website that promotes and explains the consulting service we will provide. The organization is called Bluefinch Advisory Partners. Our services include organization design, employee experience, change management, and executive coaching. I would like to see a simple clean and professional design, that reflects a modern and forward looking professional services company

Target Market(s)

Mid market and large companies

Industry/Entity Type

Management Consulting

Coding

Coded - Design and coding required

Number of Pages Required

5+ page

Font styles to use
Sans Serif

Colors

Designer to choose colors to be used in the design.

Requirements
Must have
• The following pages: Home, The Way We Work, What We Do, Our Founder, Insights, Contact.
• Search button.
• Hyper links (will be provided with main body text)
• Scrolling website with summaries at top level and links to more detail at lower level (like this website: veltracore.com)
• Company logo (uploaded)
• I have text for each of the pages that I can upload once the basic design is done
Should not have
• No clutter, keep the design clean

```html
<!DOCTYPE html>
<html lang="en">
<head>
<meta charset="utf-8">
<title>Bluefinch Advisory Partners</title>
<link rel="stylesheet" href="https://fonts.googleapis.com/css2?family=Cinzel:wght@400&family=Lato:wght@300;400;700&family=Open+Sans:wght@400;600&display=swap">
<style>
:root{
  --red:#e0212e;
  --ink:#555a5f;
  --text:#8a8d91;
  --light:#f3f3f4;
  --pink:#fbeff0;
  --dark:#1d1e20;
  --white:#fff;
}
*{box-sizing:border-box;margin:0;padding:0}
html,body{width:1200px;height:4054px;overflow:hidden}
body{position:relative;font-family:'Lato',sans-serif;color:var(--text);background:var(--white)}
section,header,footer{position:absolute;left:0;width:1200px}
.btn{position:absolute;display:flex;align-items:center;justify-content:center;font-family:'Lato',sans-serif;font-size:19px;text-transform:uppercase;text-decoration:none;letter-spacing:.3px}
.btn-red{background:var(--red);color:var(--white)}
.btn-white{background:var(--white);color:var(--red);box-shadow:0 2px 8px rgba(0,0,0,.12)}
.title{position:absolute;left:0;width:1200px;text-align:center;font-family:'Open Sans',sans-serif;font-weight:600;font-size:42px;color:var(--ink);line-height:1}
.lead{position:absolute;left:130px;width:940px;text-align:center;font-weight:300;font-size:23px;line-height:36.5px;color:var(--text)}
.copy{font-weight:300;font-size:18.5px;line-height:36.5px;color:var(--text)}
.card{position:absolute;background:var(--white);box-shadow:0 4px 22px rgba(0,0,0,.13)}

/* hero */
.hero{top:0;height:554px;background:linear-gradient(120deg,#3a3b3d 0%,#1f2022 45%,#2b2c2e 75%,#151516 100%)}
.hero-photo{position:absolute;inset:0;background:radial-gradient(ellipse at 30% 70%,rgba(120,110,100,.35),transparent 60%),radial-gradient(ellipse at 80% 30%,rgba(90,90,95,.3),transparent 55%)}
.brand{position:absolute;left:108px;top:34px;display:flex;align-items:center;gap:10px;font-family:'Lato',sans-serif;font-weight:700;font-size:21px;color:var(--red);letter-spacing:.3px;white-space:nowrap}
.brand i{width:26px;height:26px;border-radius:50%;background:var(--red);display:block}
.hero .search{left:995px;top:22px;width:89px;height:35px;font-size:16px}
.nav a{position:absolute;top:66px;font-size:16px;color:var(--white);text-decoration:none;white-space:nowrap}
.nav a.active{color:var(--red)}
.hero h1{position:absolute;left:0;top:218px;width:1200px;text-align:center;font-family:'Cinzel',serif;font-weight:400;font-size:47px;line-height:59px;color:var(--white)}
.hero .learn{left:522px;top:378px;width:156px;height:49px}

/* way */
.way{top:554px;height:735px}
.way-photo{position:absolute;left:95px;top:208px;width:500px;height:395px;background:linear-gradient(135deg,#d9d6d0,#b9b4ab 50%,#e9e7e3)}
.way .card{left:522px;top:224px;width:548px;height:363px}
.way .copy{position:absolute;left:46px;top:50px;width:460px}
.way .btn{left:46px;top:257px;width:156px;height:52px}

/* what */
.what{top:1289px;height:771px;background:linear-gradient(160deg,#f7f7f8,#ededee 50%,#f6f6f7)}
.service{position:absolute;top:345px;width:180px;text-align:center}
.ring{width:126px;height:126px;margin:0 auto;border-radius:50%;border:2px solid #e8a2a7;display:flex;align-items:center;justify-content:center}
.ring span{width:102px;height:102px;border-radius:50%;border:1px solid #eec4c7;display:flex;align-items:center;justify-content:center}
.service p{margin-top:22px;font-size:16px;line-height:25px;color:#666a6e;text-transform:uppercase}
.what .btn{left:522px;top:608px;width:156px;height:49px}

/* founder */
.founder{top:2060px;height:648px;background:linear-gradient(170deg,#fff 40%,#f4f4f5)}
.founder-photo{position:absolute;left:338px;top:335px;width:238px;height:200px;background:linear-gradient(160deg,#e3ddd2,#b8a994 60%,#8a9bb3);box-shadow:0 3px 10px rgba(0,0,0,.2)}
.founder h3{position:absolute;left:580px;top:358px;width:350px;text-align:center;font-family:'Open Sans',sans-serif;font-weight:600;font-size:34px;color:var(--ink)}
.founder h4{position:absolute;left:580px;top:404px;width:350px;text-align:center;font-family:'Open Sans',sans-serif;font-weight:400;font-size:29px;color:#777}
.founder .btn{left:692px;top:465px;width:127px;height:40px;font-size:16px}

/* insights */
.insights{top:2708px;height:725px;background:linear-gradient(150deg,#fdf3f4,#f9e8ea 55%,#fcf1f2)}
.ins-photo{position:absolute;left:584px;top:219px;width:497px;height:395px;background:linear-gradient(120deg,#d8d5d0,#b9c3d1 55%,#e2e1de)}
.insights .card{left:68px;top:233px;width:551px;height:367px}
.insights .copy{position:absolute;left:49px;top:50px;width:460px}
.insights .btn{left:48px;top:262px;width:157px;height:49px}

/* contact */
.contact{top:3433px;height:519px}
.contact .lead{top:162px}
.item{position:absolute;top:270px;display:flex;align-items:flex-start;gap:12px;font-size:16px;line-height:27px;color:#666a6e;white-space:nowrap}
.dot{width:38px;height:38px;border-radius:50%;border:1.5px solid #e8a2a7;display:flex;align-items:center;justify-content:center;flex:none}
.contact .btn{left:514px;top:373px;width:170px;height:48px}

/* footer */
.foot{top:3952px;height:102px;background:var(--dark)}
.foot a{position:absolute;top:40px;font-size:13px;font-weight:700;color:var(--white);text-decoration:none;white-space:nowrap}
.foot small{position:absolute;left:862px;top:40px;font-size:13px;color:#bbb;white-space:nowrap}
</style>
</head>
<body>

<header class="hero">
  <div class="hero-photo" role="img" aria-label="Dark photo of business people meeting around a table"></div>
  <div class="brand"><i></i>Bluefinch Advisory Partners</div>
  <a class="btn btn-red search" href="#">Search</a>
  <nav class="nav">
    <a class="active" style="left:511px" href="#">Home</a>
    <a style="left:581px" href="#">The Way We Work</a>
    <a style="left:730px" href="#">What We Do</a>
    <a style="left:838px" href="#">Our Founder</a>
    <a style="left:951px" href="#">Insights</a>
    <a style="left:1033px" href="#">Contact</a>
  </nav>
  <h1>We are organisation &amp; people<br>consulting firm</h1>
  <a class="btn btn-white learn" href="#">Learn More</a>
</header>

<section class="way">
  <h2 class="title" style="top:109px">The Way We Work</h2>
  <div class="way-photo" role="img" aria-label="Photo of consultants meeting with a couple around a laptop"></div>
  <div class="card">
    <p class="copy">Lorem ipsum dolor sit amet, consectetur ad ipiscing elit, sed do eiusmod tempor incidi dunt ut labore et dolore magna aliqua. Ut enim ad mainim veniam, quis nostrud exer citea tion ual lamco laboris nisi ut aliquip ex ea commodo consequat.</p>
    <a class="btn btn-red" href="#">Learn More</a>
  </div>
</section>

<section class="what">
  <h2 class="title" style="top:107px">What We Do</h2>
  <p class="lead" style="top:182px">Lorem ipsum dolor sit amet, consectetur adipiscing elit, sed do eiusmod tempor incidi dunt ut labore et dolore magna aliqua. Ut enim ad mainim veniam, quis nostrud exercita tion ual lamco laboris nisi ut aliquip ex ea commodo consequat.</p>

  <div class="service" style="left:156px">
    <div class="ring"><span>
      <svg width="44" height="48" viewBox="0 0 44 48" fill="none" stroke="#e0212e" stroke-width="2"><rect x="8" y="6" width="28" height="38" rx="2"/><rect x="16" y="2" width="12" height="7" rx="1"/><path d="M14 18h16M14 25h16M14 32h16M14 39h10"/></svg>
    </span></div>
    <p>Organisation<br>Design</p>
  </div>
  <div class="service" style="left:391px">
    <div class="ring"><span>
      <svg width="50" height="50" viewBox="0 0 50 50" fill="none" stroke="#e0212e" stroke-width="2"><polygon points="25,4 44,15 44,35 25,46 6,35 6,15"/><circle cx="25" cy="20" r="6" fill="#e0212e"/><path d="M14 36c2-7 20-7 22 0" fill="#e0212e"/></svg>
    </span></div>
    <p>Employee<br>Experience</p>
  </div>
  <div class="service" style="left:626px">
    <div class="ring"><span>
      <svg width="50" height="50" viewBox="0 0 50 50" fill="none" stroke="#e0212e" stroke-width="3"><circle cx="19" cy="29" r="9"/><circle cx="19" cy="29" r="3" fill="#e0212e"/><circle cx="34" cy="16" r="6"/><path d="M19 16v-4M19 46v-4M6 29h4M28 29h4M38 32c2 6-2 10-8 12M10 12c4-4 10-5 14-3"/></svg>
    </span></div>
    <p>Change<br>Management</p>
  </div>
  <div class="service" style="left:859px">
    <div class="ring"><span>
      <svg width="50" height="50" viewBox="0 0 50 50" fill="none" stroke="#e0212e" stroke-width="2"><rect x="6" y="8" width="38" height="26"/><path d="M12 28l8-8 6 5 10-11M25 34v6M18 44l7-4 7 4"/></svg>
    </span></div>
    <p>Executive<br>Coaching</p>
  </div>

  <a class="btn btn-white" href="#">Learn More</a>
</section>

<section class="founder">
  <h2 class="title" style="top:101px">Our Founder</h2>
  <p class="lead" style="top:176px">Lorem ipsum dolor sit amet, consectetur adipiscing elit, sed do eiusmod tempor incidi dunt ut labore et dolore magna aliqua. Ut enim ad mainim veniam, quis nostrud exercita tion ual lamco laboris nisi ut aliquip ex ea commodo consequat.</p>
  <div class="founder-photo" role="img" aria-label="Portrait photo of the founder"></div>
  <h3>Julian Marsh</h3>
  <h4>Founder</h4>
  <a class="btn btn-red" href="#">Learn More</a>
</section>

<section class="insights">
  <h2 class="title" style="top:118px">Our Insights</h2>
  <div class="ins-photo" role="img" aria-label="Photo of colleagues shaking hands in an office"></div>
  <div class="card">
    <p class="copy">Lorem ipsum dolor sit amet, consectetur ad ipiscing elit, sed do eiusmod tempor incidi dunt ut labore et dolore magna aliqua. Ut enim ad mainim veniam, quis nostrud exer citea tion ual lamco laboris nisi ut aliquip ex ea commodo consequat.</p>
    <a class="btn btn-red" href="#">Learn More</a>
  </div>
</section>

<section class="contact">
  <h2 class="title" style="top:96px">Contact Bluefinch</h2>
  <p class="lead">Ut labore et dolore magna aliqua. Ut enim ad mainim veniam, quis nostrud exercita tion ual lamco laboris nisi ut aliquip ex ea commodo consequat.</p>
  <div class="item" style="left:140px">
    <span class="dot"><svg width="14" height="18" viewBox="0 0 14 18"><path d="M7 0C3 0 0 3 0 7c0 5 7 11 7 11s7-6 7-11c0-4-3-7-7-7z" fill="#e0212e"/><circle cx="7" cy="7" r="2.5" fill="#fff"/></svg></span>
    <span>48 Harbor Lane, Millbrook,<br>CT 06512, U. S. A.</span>
  </div>
  <div class="item" style="left:438px">
    <span class="dot"><svg width="18" height="13" viewBox="0 0 18 13"><rect width="18" height="13" rx="1" fill="#e0212e"/><path d="M1 1l8 6 8-6" stroke="#fff" stroke-width="1.4" fill="none"/></svg></span>
    <span>mara.quill@bluefinchadvisorypartners.com</span>
  </div>
  <div class="item" style="left:905px">
    <span class="dot"><svg width="16" height="16" viewBox="0 0 16 16"><path d="M3 1l3 3-2 2c1 2 3 4 5 5l2-2 3 3-2 3C7 15 1 9 0 4z" fill="#e0212e"/></svg></span>
    <span>1-555-014-2290</span>
  </div>
  <a class="btn btn-red" href="#">Get In Touch</a>
</section>

<footer class="foot">
  <a style="left:119px" href="#">Home</a>
  <a style="left:178px" href="#">The Way We Work</a>
  <a style="left:314px" href="#">What We Do</a>
  <a style="left:414px" href="#">Our Founder</a>
  <a style="left:514px" href="#">Insights</a>
  <a style="left:589px" href="#">Contact</a>
  <small>Copyright © 2018 . All Rights Reserved</small>
</footer>

</body>
</html>
```